Fitness Equipment & Service

I want to make the card eye catching and fun. We are called Corvane Motion Limited and we are based in Wales. We sell, install and service all types of fitness equipment from Skipping ropes, right through the Dumbbells, Kettle bells and Barbells through to state of the art Treadmills, Running Machines and Strength Equipment. We also design and install changing room furniture and lockers.

TYPOGRAPHY
We would like to use Futrura. Futura has an appearance of efficiency and forwardness. The typeface is derived
from simple geometric forms (near-perfect circles, triangles and squares) and is based on strokes of
near-even weight, which are low in contrast. This is most visible in the almost perfectly round stroke of
the o, which is nonetheless slightly ovoid.
The lowercase has tall ascenders, which rise above the cap line. The uppercase
characters present proportions similar to those of classical Roman capitals.

TYPOGRAPHIC CONSIDERATIONS
No Strike though
No Horizontal Scaling
No Drop Shadows
No Effects
Never use less than 120% Leading

OUR CORPORATE COLOURS
BRAND GUIDELINES
We were thinking that our primary colour palette consists of the Acid Green (Pantone 382) and Process Black.

We work closely with tquarly Ltd and would like to include their name on the card somewhere. I have attached images of the other brands that we work with as an idea or the small icons I have included that illustrate what we do?. I have very kindly been given permission to use any of the images off the files that I have included below, so I hope these help. I will include these below. I would be open to suggestions if it made the card more striking Can you do it?
Updates

Hi All, Just wanted to add a few thoughts but you are the guys with the creative visions (thats why are here) We are based in Wales, UK and we would be open to lots of different ideas on a theme but must be eye catching, Bold and FUN. If you can or think that the Welsh or any dragon could be put in there then go for it (its not a must have) We have also added some ideas for colour but again its over to you!! GO FOR IT ! Thanks and look forward to your visions! Owen

Hi All, Just thought I would sen through the contact details that need to be on the card. (if you want to play around with icons instead of the wording twitter, Facebook, go for it): Corvane Motion Limited Owen Pritchard Managing Director Mob: +44 (0)7582 913 406 e-mail: sales@corvanemotion.co.uk Web: Corvanemotion.co.uk twitter: @motionLetterbin Facebook: Corvane Motion Limited

```html
<!DOCTYPE html>
<html lang="en">
<head>
<meta charset="utf-8">
<title>Corvane Motion Limited — Business Card</title>
<link rel="stylesheet" href="https://fonts.googleapis.com/css2?family=Arimo:wght@400;700&display=swap">
<style>
  :root {
    --canvas: #e9e6e1;
    --navy: #161d5c;
    --navy-deep: #0f1445;
    --paper: #f4f4f2;
    --gold: #c9a53a;
    --ink-navy: #232a6e;
    --white: #ffffff;
    --sky: #2f8fdc;
    --sky-deep: #1767b5;
    --sky-light: #52c3ea;
  }
  * { box-sizing: border-box; margin: 0; padding: 0; }
  html, body {
    width: 1200px; height: 892px; overflow: hidden;
    background: var(--canvas);
    font-family: "Arimo", Arial, sans-serif;
  }
  .stage {
    width: 1200px; height: 892px;
    display: flex; align-items: center; justify-content: center; gap: 40px;
  }
  .card {
    position: relative;
    width: 540px; height: 309px;
    overflow: hidden;
    box-shadow: 0 6px 18px rgba(0,0,0,.18);
  }
  /* Front */
  .card-front { background: var(--navy); }
  .card-front .split { position: absolute; inset: 0; width: 100%; height: 100%; }
  .brand-block {
    position: absolute; left: 34px; top: 110px; width: 180px;
    display: flex; flex-direction: column; align-items: flex-start; gap: 14px;
  }
  .brand-dot {
    width: 70px; height: 70px; border-radius: 50%;
    background: var(--ink-navy);
  }
  .brand-name {
    font-weight: 700; font-size: 22px; line-height: 1.2;
    color: var(--ink-navy);
  }
  .identity {
    position: absolute; right: 30px; top: 26px; text-align: right;
  }
  .person-name {
    font-size: 30px; font-weight: 400; color: var(--gold); line-height: 1.2;
  }
  .person-role {
    font-size: 15px; color: var(--white); line-height: 1.2;
  }
  .contacts {
    position: absolute; right: 30px; bottom: 26px;
    list-style: none; text-align: right;
  }
  .contacts li {
    display: flex; align-items: center; justify-content: flex-end; gap: 10px;
    font-size: 14px; line-height: 1.5; color: var(--white);
  }
  .contacts .marker {
    width: 9px; height: 9px; background: var(--gold); flex: none;
  }
  /* Back */
  .card-back .tiles {
    position: absolute; inset: 0;
    background: linear-gradient(135deg, var(--sky-light) 0%, var(--sky) 45%, var(--sky-deep) 100%);
  }
  .back-brand {
    position: absolute; left: 0; right: 0; top: 50%; transform: translateY(-50%);
    text-align: center;
    font-weight: 700; font-size: 38px; line-height: 1.2; color: var(--white);
  }
</style>
</head>
<body>
<main class="stage">
  <section class="card card-front" aria-label="Business card front">
    <svg class="split" viewBox="0 0 540 309" preserveAspectRatio="none" aria-hidden="true">
      <path d="M0 0 H190 Q250 150 215 309 H0 Z" fill="var(--paper)"/>
      <path d="M190 0 Q250 150 215 309" fill="none" stroke="var(--gold)" stroke-width="4"/>
    </svg>
    <div class="brand-block">
      <span class="brand-dot"></span>
      <span class="brand-name">Corvane Motion Limited</span>
    </div>
    <div class="identity">
      <p class="person-name">Owen Pritchard</p>
      <p class="person-role">Managing Director</p>
    </div>
    <ul class="contacts">
      <li>@motionLetterbin <span class="marker"></span></li>
      <li>+44 (0)7582 913 406 <span class="marker"></span></li>
      <li>Corvanemotion.co.uk <span class="marker"></span></li>
      <li>Corvane Motion Limited <span class="marker"></span></li>
      <li>sales@corvanemotion.co.uk <span class="marker"></span></li>
    </ul>
  </section>

  <section class="card card-back" aria-label="Business card back">
    <div class="tiles" role="img" aria-label="Blue tiled backdrop with fitness equipment icons"></div>
    <p class="back-brand">Corvane Motion Limited</p>
  </section>
</main>
</body>
</html>
```